Application page web design and internal pages

Create a web site where home
Page looks like an application screen for a mobile phone

Use bold icons and colors with images that have round edges

PorlenPurse Apps is name of page

Search bar at the top

Use colors from Vextaro.org for background

Price of ZORBS in top right corner (https://www.quelvix.example/trade/en-US?symbol=ZORBS_USDT&layout=basic&theme=dark)

Pages within each app should be the same color as the icon

Use the following as app icons on the page:
Key
Icon name: first screen; second screen (text)

⁃ Balances: enter pin; display balances (Your account can hold multiple currency denominations. Your balances are: ZORBS 1234567890)
⁃ Transactions: enter pin; display transactions (Your last 5 payments are ZORBS 10 from Vextaro)
⁃ Send Money: enter phone number, enter amount, send button; display message
⁃ Create Account: choose country code, enter phone number, create button; enter pin; display message ( (phone number) will be notified when their account has been created)
⁃ My Wallet Address: enter pin; display public key (IMPORTANT Send only STELLAR blockchain tokens to this deposit address: GDXQ7PLM2ZNVA9TRK4WSEY8HCBUJ6FOGDLIXP3QM5RTVKNAWZEHOBCYS)
⁃ Private Message: enter phone number, enter message, choose image, send button; enter pin; display message ( (phone number) will be notified when their message has been created)
⁃ Buy Cryptocurrency: drop drown menu of cryptocurrency to purchase (Bitcoin/Ethereum/Stellar/ZORBS), Amount in USD field, amount in chosen cryptocurrency displayed, frequency drop down menu (once/daily/weekly/monthly), buy button; enter card information (name, card number, expiration date, cvv, billing address, zip code), confirm buy button, transactions will appear on your billing statement as VEXTARO; enter pin screen; display message (You will be notified when your coin is received)
⁃ NFTs: upload image, title, description, link media, create NFT button; enter pin screen; display message (You will be notified when your NFT is created)
⁃ Earn: display message (Earn cryptocurrency doing what you do everyday, coming soon)
⁃ Files/Vault: display message (Storage for your photos, documents and more, coming soon)
⁃ Wealth: display message (Build wealth by working with a financial professional to get you to the next level), check box (I would like a financial professional to contact me about building wealth), contact me button; display message (A financial professional will contact you to achieve your financial goals)
⁃ Education: display message (Learn more about everything, coming soon)
⁃ News: display message (News from around the world, coming soon)
⁃ FAQs: use FAQs from this link https://vextaro.example/faq
⁃ Contact Us: enter message, send button; display message (Thank you for reaching out. We will reply to your message in the order it was received. Your patience is appreciated. Blessings.)

Requirements
Must have
• Application home page that looks like the Home Screen of a mobile phone
Nice to have
• Colorful icons

```html
<!DOCTYPE html>
<html lang="en">
<head>
<meta charset="utf-8">
<title>PorlenPurse Apps — My Wallet Address &amp; Private Message</title>
<link rel="stylesheet" href="https://fonts.googleapis.com/css2?family=Roboto:wght@400;500;700;900&family=Roboto+Condensed:wght@700&family=Poppins:wght@400;500&display=swap">
<style>
  :root {
    --board: #bdbec0;
    --ink: #0b0b0b;
    --navy: #15163a;
    --white: #ffffff;
    --muted: #5d5d66;
    --line: #bfc2c8;
    --success: #3ecf6a;
  }
  * { box-sizing: border-box; margin: 0; padding: 0; }
  html, body { width: 1200px; height: 1134px; overflow: hidden; background: var(--board); }
  .board { position: relative; width: 1200px; height: 1134px; font-family: "Roboto", sans-serif; }
  .section-title {
    position: absolute; left: 117px; line-height: 1;
    font-family: "Roboto", sans-serif; font-weight: 900; font-size: 32px;
    letter-spacing: -0.3px; color: var(--ink);
  }
  .screen-slot { position: absolute; width: 202px; height: 393px; overflow: hidden; }
  .screen {
    position: relative; width: 335px; height: 650px; background: var(--white);
    transform: scale(0.603); transform-origin: 0 0; overflow: hidden; line-height: 1.2;
  }
  .screen__backdrop { position: absolute; inset: 0; width: 335px; height: 650px; }
  .brand-mark {
    position: absolute; top: 68px; left: 159px; width: 17px; height: 15px;
    border: 1.5px solid var(--white); border-radius: 3px;
  }
  .brand {
    position: absolute; top: 99px; left: 0; width: 100%; text-align: center; line-height: 18px;
    color: var(--white); font-weight: 500; font-size: 15px; letter-spacing: 2.6px;
  }
  .price-bar {
    position: absolute; left: 69px; top: 136px; width: 196px; height: 49px;
    background: var(--navy); color: var(--white); border-radius: 2px;
    display: flex; align-items: center; justify-content: space-between; padding: 0 22px 0 19px;
    font-size: 13px; box-shadow: 0 3px 6px rgba(0,0,0,.25);
  }
  .price-bar__caret { font-size: 8px; margin-left: 6px; }
  .price-bar__arrow { margin-left: 8px; font-size: 12px; }
  .search {
    position: absolute; left: 33px; top: 209px; width: 267px; height: 36px;
    background: var(--white); border-radius: 2px; box-shadow: 0 2px 8px rgba(0,0,0,.18);
    display: flex; align-items: center; justify-content: space-between; padding-left: 11px;
    font-family: "Poppins", sans-serif; font-size: 8px; color: #333;
  }
  .search__button {
    width: 32px; height: 32px; margin-right: 2px; background: var(--navy); border-radius: 3px;
    display: flex; align-items: center; justify-content: center;
  }
  .menu-icon { position: absolute; left: 29px; top: 287px; }
  .screen-heading {
    position: absolute; left: 0; width: 100%; text-align: center;
    font-weight: 500; font-size: 15px; color: #111;
  }
  .prompt { position: absolute; left: 0; width: 100%; text-align: center; font-size: 12px; color: var(--muted); }
  .pin-row { position: absolute; left: 0; width: 100%; display: flex; justify-content: center; gap: 26px; }
  .pin-row span { display: block; width: 33px; height: 1px; background: var(--line); }
  .send-button {
    position: absolute; left: 50%; width: 120px; height: 32px; margin-left: -60px;
    background: var(--navy); color: var(--white); border-radius: 16px;
    display: flex; align-items: center; justify-content: center;
    font-weight: 700; font-size: 12px;
  }
  .wallet-key {
    position: absolute; left: 0; top: 347px; width: 100%; text-align: center;
    font-family: "Roboto Condensed", sans-serif; font-weight: 700; font-size: 7.4px; color: #111;
  }
  .field-label { position: absolute; left: 32px; font-size: 11.5px; color: var(--muted); }
  .field-input {
    position: absolute; left: 32px; width: 232px; height: 40px;
    border: 1px solid #b9bcc4; border-radius: 3px; background: var(--white);
  }
  .file-icon { position: absolute; left: 252px; top: 506px; }
  .success-tick { position: absolute; left: 152px; top: 352px; }
  .success-text {
    position: absolute; left: 30px; top: 400px; width: 275px; text-align: center;
    font-size: 12px; line-height: 18px; color: var(--muted);
  }
  .legal {
    position: absolute; left: 0; top: 597px; width: 100%; text-align: center;
    font-family: "Poppins", sans-serif; font-size: 6.5px; color: #333;
  }
  .tab-bar {
    position: absolute; left: 0; bottom: 0; width: 100%; height: 33px; background: var(--navy);
    display: flex; align-items: center; justify-content: center;
  }
</style>
</head>
<body>
<main class="board">

  <h2 class="section-title" style="top:62px;">MY WALLET ADDRESS</h2>

  <!-- Wallet address: pin entry -->
  <div class="screen-slot" style="left:121px; top:133px;">
    <section class="screen">
      <svg class="screen__backdrop" viewBox="0 0 335 650" aria-hidden="true">
        <defs>
          <linearGradient id="hdr1" x1="0" y1="0" x2="1" y2="1">
            <stop offset="0" stop-color="#1b2447"/><stop offset=".55" stop-color="#18566f"/><stop offset="1" stop-color="#25b3c9"/>
          </linearGradient>
        </defs>
        <rect width="335" height="300" fill="url(#hdr1)"/>
        <path d="M0,0 C30,95 110,138 200,142 C285,146 322,205 335,262 L335,650 L0,650 Z" fill="#fff"/>
      </svg>
      <span class="brand-mark"></span>
      <div class="brand">PORLENPURSE</div>
      <div class="price-bar"><span>ZORBS<span class="price-bar__caret">&#8964;</span></span><span>$ 5.98<span class="price-bar__arrow">&#8593;</span></span></div>
      <div class="search">Search Here<span class="search__button"><svg width="18" height="18" viewBox="0 0 18 18"><circle cx="8" cy="8" r="6" fill="none" stroke="#fff" stroke-width="1.4"/><line x1="12.3" y1="12.3" x2="16" y2="16" stroke="#fff" stroke-width="1.4"/></svg></span></div>
      <svg class="menu-icon" width="24" height="18" viewBox="0 0 24 18" aria-hidden="true"><rect y="1" width="24" height="2.4" fill="#15163a"/><rect y="8" width="24" height="2.4" fill="#15163a"/><rect y="15" width="24" height="2.4" fill="#15163a"/></svg>
      <h3 class="screen-heading" style="top:324px;">MY WALLET ADDRESS</h3>
      <p class="prompt" style="top:360px;">Enter Your Pin Here</p>
      <div class="pin-row" style="top:411px;"><span></span><span></span><span></span><span></span></div>
      <div class="send-button" style="top:442px;">SEND</div>
      <p class="legal">©Vextaro Zero Liability Transaction Policy</p>
      <nav class="tab-bar"><svg width="14" height="13" viewBox="0 0 14 13"><path d="M7 0 L14 6.5 L12 6.5 L12 13 L8.5 13 L8.5 9 L5.5 9 L5.5 13 L2 13 L2 6.5 L0 6.5 Z" fill="#fff"/></svg></nav>
    </section>
  </div>

  <!-- Wallet address: public key -->
  <div class="screen-slot" style="left:379px; top:133px;">
    <section class="screen">
      <svg class="screen__backdrop" viewBox="0 0 335 650" aria-hidden="true">
        <defs>
          <linearGradient id="hdr2" x1="0" y1="0" x2="1" y2="1">
            <stop offset="0" stop-color="#1b2447"/><stop offset=".55" stop-color="#18566f"/><stop offset="1" stop-color="#25b3c9"/>
          </linearGradient>
        </defs>
        <rect width="335" height="300" fill="url(#hdr2)"/>
        <path d="M0,0 C30,95 110,138 200,142 C285,146 322,205 335,262 L335,650 L0,650 Z" fill="#fff"/>
      </svg>
      <span class="brand-mark"></span>
      <div class="brand">PORLENPURSE</div>
      <div class="price-bar"><span>ZORBS<span class="price-bar__caret">&#8964;</span></span><span>$ 5.98<span class="price-bar__arrow">&#8593;</span></span></div>
      <div class="search">Search Here<span class="search__button"><svg width="18" height="18" viewBox="0 0 18 18"><circle cx="8" cy="8" r="6" fill="none" stroke="#fff" stroke-width="1.4"/><line x1="12.3" y1="12.3" x2="16" y2="16" stroke="#fff" stroke-width="1.4"/></svg></span></div>
      <svg class="menu-icon" width="24" height="18" viewBox="0 0 24 18" aria-hidden="true"><rect y="1" width="24" height="2.4" fill="#15163a"/><rect y="8" width="24" height="2.4" fill="#15163a"/><rect y="15" width="24" height="2.4" fill="#15163a"/></svg>
      <p class="prompt" style="top:317px; color:#444;">Blockchain Tokens</p>
      <p class="wallet-key">GDXQ7PLM2ZNVA9TRK4WSEY8HCBUJ6FOGDLIXP3QM5RTVKNAWZEHOBCYS</p>
      <p class="legal">©Vextaro Zero Liability Transaction Policy</p>
      <nav class="tab-bar"><svg width="14" height="13" viewBox="0 0 14 13"><path d="M7 0 L14 6.5 L12 6.5 L12 13 L8.5 13 L8.5 9 L5.5 9 L5.5 13 L2 13 L2 6.5 L0 6.5 Z" fill="#fff"/></svg></nav>
    </section>
  </div>

  <h2 class="section-title" style="top:584px; left:115px;">PRIVATE MESSAGE</h2>

  <!-- Private message: compose -->
  <div class="screen-slot" style="left:120px; top:655px;">
    <section class="screen">
      <svg class="screen__backdrop" viewBox="0 0 335 650" aria-hidden="true">
        <defs>
          <linearGradient id="hdr3" x1="0" y1="0" x2="1" y2="1">
            <stop offset="0" stop-color="#1b2447"/><stop offset=".55" stop-color="#18566f"/><stop offset="1" stop-color="#25b3c9"/>
          </linearGradient>
        </defs>
        <rect width="335" height="300" fill="url(#hdr3)"/>
        <path d="M0,0 C30,95 110,138 200,142 C285,146 322,205 335,262 L335,650 L0,650 Z" fill="#fff"/>
      </svg>
      <span class="brand-mark"></span>
      <div class="brand">PORLENPURSE</div>
      <div class="price-bar"><span>ZORBS<span class="price-bar__caret">&#8964;</span></span><span>$ 5.98<span class="price-bar__arrow">&#8593;</span></span></div>
      <div class="search">Search Here<span class="search__button"><svg width="18" height="18" viewBox="0 0 18 18"><circle cx="8" cy="8" r="6" fill="none" stroke="#fff" stroke-width="1.4"/><line x1="12.3" y1="12.3" x2="16" y2="16" stroke="#fff" stroke-width="1.4"/></svg></span></div>
      <svg class="menu-icon" width="24" height="18" viewBox="0 0 24 18" aria-hidden="true"><rect y="1" width="24" height="2.4" fill="#15163a"/><rect y="8" width="24" height="2.4" fill="#15163a"/><rect y="15" width="24" height="2.4" fill="#15163a"/></svg>
      <h3 class="screen-heading" style="top:292px;">PRIVATE MESSAGE</h3>
      <label class="field-label" style="top:334px;">Enter Phone Number</label>
      <div class="field-input" style="top:360px;"></div>
      <label class="field-label" style="top:413px;">Enter Message</label>
      <div class="field-input" style="top:440px;"></div>
      <label class="field-label" style="top:502px;">Choose Image</label>
      <svg class="file-icon" width="12" height="15" viewBox="0 0 12 15" aria-hidden="true"><path d="M0 0 H8 L12 4 V15 H0 Z" fill="#15163a"/><path d="M6 12 V6.5 M3.6 8.8 L6 6.3 L8.4 8.8" stroke="#fff" stroke-width="1.2" fill="none"/><line x1="3" y1="13" x2="9" y2="13" stroke="#fff" stroke-width="1"/></svg>
      <div class="send-button" style="top:545px;">SEND</div>
      <p class="legal">©Vextaro Zero Liability Transaction Policy</p>
      <nav class="tab-bar"><svg width="14" height="13" viewBox="0 0 14 13"><path d="M7 0 L14 6.5 L12 6.5 L12 13 L8.5 13 L8.5 9 L5.5 9 L5.5 13 L2 13 L2 6.5 L0 6.5 Z" fill="#fff"/></svg></nav>
    </section>
  </div>

  <!-- Private message: pin entry -->
  <div class="screen-slot" style="left:377px; top:655px;">
    <section class="screen">
      <svg class="screen__backdrop" viewBox="0 0 335 650" aria-hidden="true">
        <defs>
          <linearGradient id="hdr4" x1="0" y1="0" x2="1" y2="1">
            <stop offset="0" stop-color="#1b2447"/><stop offset=".55" stop-color="#18566f"/><stop offset="1" stop-color="#25b3c9"/>
          </linearGradient>
        </defs>
        <rect width="335" height="300" fill="url(#hdr4)"/>
        <path d="M0,0 C30,95 110,138 200,142 C285,146 322,205 335,262 L335,650 L0,650 Z" fill="#fff"/>
      </svg>
      <span class="brand-mark"></span>
      <div class="brand">PORLENPURSE</div>
      <div class="price-bar"><span>ZORBS<span class="price-bar__caret">&#8964;</span></span><span>$ 5.98<span class="price-bar__arrow">&#8593;</span></span></div>
      <div class="search">Search Here<span class="search__button"><svg width="18" height="18" viewBox="0 0 18 18"><circle cx="8" cy="8" r="6" fill="none" stroke="#fff" stroke-width="1.4"/><line x1="12.3" y1="12.3" x2="16" y2="16" stroke="#fff" stroke-width="1.4"/></svg></span></div>
      <svg class="menu-icon" width="24" height="18" viewBox="0 0 24 18" aria-hidden="true"><rect y="1" width="24" height="2.4" fill="#15163a"/><rect y="8" width="24" height="2.4" fill="#15163a"/><rect y="15" width="24" height="2.4" fill="#15163a"/></svg>
      <p class="prompt" style="top:359px;">Enter Your Pin Here</p>
      <div class="pin-row" style="top:410px;"><span></span><span></span><span></span><span></span></div>
      <div class="send-button" style="top:442px;">SEND</div>
      <p class="legal">©Vextaro Zero Liability Transaction Policy</p>
      <nav class="tab-bar"><svg width="14" height="13" viewBox="0 0 14 13"><path d="M7 0 L14 6.5 L12 6.5 L12 13 L8.5 13 L8.5 9 L5.5 9 L5.5 13 L2 13 L2 6.5 L0 6.5 Z" fill="#fff"/></svg></nav>
    </section>
  </div>

  <!-- Private message: confirmation -->
  <div class="screen-slot" style="left:638px; top:655px;">
    <section class="screen">
      <svg class="screen__backdrop" viewBox="0 0 335 650" aria-hidden="true">
        <defs>
          <linearGradient id="hdr5" x1="0" y1="0" x2="1" y2="1">
            <stop offset="0" stop-color="#1b2447"/><stop offset=".55" stop-color="#18566f"/><stop offset="1" stop-color="#25b3c9"/>
          </linearGradient>
        </defs>
        <rect width="335" height="300" fill="url(#hdr5)"/>
        <path d="M0,0 C30,95 110,138 200,142 C285,146 322,205 335,262 L335,650 L0,650 Z" fill="#fff"/>
      </svg>
      <span class="brand-mark"></span>
      <div class="brand">PORLENPURSE</div>
      <div class="price-bar"><span>ZORBS<span class="price-bar__caret">&#8964;</span></span><span>$ 5.98<span class="price-bar__arrow">&#8593;</span></span></div>
      <div class="search">Search Here<span class="search__button"><svg width="18" height="18" viewBox="0 0 18 18"><circle cx="8" cy="8" r="6" fill="none" stroke="#fff" stroke-width="1.4"/><line x1="12.3" y1="12.3" x2="16" y2="16" stroke="#fff" stroke-width="1.4"/></svg></span></div>
      <svg class="menu-icon" width="24" height="18" viewBox="0 0 24 18" aria-hidden="true"><rect y="1" width="24" height="2.4" fill="#15163a"/><rect y="8" width="24" height="2.4" fill="#15163a"/><rect y="15" width="24" height="2.4" fill="#15163a"/></svg>
      <svg class="success-tick" width="32" height="32" viewBox="0 0 32 32" aria-hidden="true"><circle cx="16" cy="16" r="14.5" fill="none" stroke="#3ecf6a" stroke-width="2.2"/><path d="M9.5 16.5 L14 21 L22.5 11.5" fill="none" stroke="#3ecf6a" stroke-width="2.2" stroke-linecap="round" stroke-linejoin="round"/></svg>
      <p class="success-text">Your phone number will be notified when their message has been created</p>
      <p class="legal">©Vextaro Zero Liability Transaction Policy</p>
      <nav class="tab-bar"><svg width="14" height="13" viewBox="0 0 14 13"><path d="M7 0 L14 6.5 L12 6.5 L12 13 L8.5 13 L8.5 9 L5.5 9 L5.5 13 L2 13 L2 6.5 L0 6.5 Z" fill="#fff"/></svg></nav>
    </section>
  </div>

</main>
</body>
</html>
```